Design a WordPress layout for a home loans company

The home loans company in question is going through a rebrand and needs a new website layout.
Sites they like: http://www.brightkeylending.com.au/
Current logo: Attached.
Colours to be used: As per those used in logo.
Primary: #71aa3d
Secondary: #130e10
Pages to be designed:
- Homepage
- Internal services page
Menu items for display purposes:
- Home
- About Us
- Speak to a Broker
- Articles
- Contact Us
A modern design with simplicity is key.
For copy, dummy text such as Lorem ipsum will be fine.
If you would like anything elso, please ask.
Target Market(s)
25-40 year old
Mostly female
Buying their first home in most cases
Industry/Entity Type
Mortgage Brokerage
Number of Pages Required
2 page

```html
<!DOCTYPE html>
<html lang="en">
<head>
<meta charset="utf-8">
<title>Maple Home Loans</title>
<link href="https://fonts.googleapis.com/css2?family=Raleway:wght@500;600;700&family=Open+Sans:wght@400;600;700&display=swap" rel="stylesheet">
<style>
:root{
  --green:#71aa3d;
  --green-dark:#5e9330;
  --ink:#130e10;
  --text:#222;
  --muted:#666;
  --line:#d6d6d6;
  --light:#f1f1f1;
  --white:#fff;
}
*{margin:0;padding:0;box-sizing:border-box}
html,body{width:1200px;height:3529px;overflow:hidden}
body{position:relative;background:var(--white);font-family:"Open Sans",sans-serif;color:var(--text)}
.abs{position:absolute}
h1,h2,h3,h4{font-family:"Raleway",sans-serif}

/* header */
.site-header{left:0;top:0;width:1200px;height:100px;background:var(--white)}
.brand{left:97px;top:28px;font-family:"Raleway",sans-serif;font-weight:700;font-size:34px;color:var(--green);display:flex;align-items:center;gap:10px;white-space:nowrap}
.brand-mark{width:18px;height:18px;background:var(--green);flex:none}
.top-contact{right:97px;top:22px;font-size:15px;color:#333;display:flex;gap:12px;align-items:center}
.top-contact svg{vertical-align:-3px;margin-right:6px}
.main-nav{right:97px;top:64px;display:flex;gap:38px;font-family:"Raleway",sans-serif;font-weight:600;font-size:15px;color:#222;align-items:center}
.main-nav .active{color:var(--green)}

/* hero */
.hero{left:0;top:100px;width:1200px;height:572px;background:linear-gradient(100deg,#6b5a4c 0%,#a88a70 40%,#c9b39a 65%,#5a5048 100%)}
.hero-title{left:97px;top:232px;font-size:58px;font-weight:700;color:var(--white);font-family:"Raleway",sans-serif}
.hero-sub{left:97px;top:314px;font-size:26px;color:var(--white)}
.search{left:97px;top:384px;width:546px;height:56px;display:flex}
.search-input{flex:1;background:var(--white);display:flex;align-items:center;padding-left:20px;font-size:15px;color:#666;gap:8px}
.search-btn{width:150px;background:var(--green);color:var(--white);font-weight:700;font-size:16px;display:flex;align-items:center;justify-content:center}
.dots{left:570px;top:511px;display:flex;gap:6px}
.dots span{width:11px;height:11px;border-radius:50%;border:2px solid var(--white)}
.dots span:first-child{background:var(--white)}
.hero-curve{left:0;top:610px}

/* section headings */
.section-title{width:1200px;left:0;text-align:center;font-size:34px;font-weight:700;color:var(--ink)}
.section-text{width:800px;left:200px;text-align:center;font-size:14px;line-height:26px;color:var(--muted)}

/* features */
.feature{width:233px;height:257px;top:842px;border:2px solid var(--line);text-align:center}
.feature-icon{width:100px;height:100px;border-radius:50%;background:var(--green);margin:28px auto 0;display:flex;align-items:center;justify-content:center}
.feature h3{font-size:20px;font-weight:700;margin-top:22px;color:var(--ink)}
.feature p{font-size:13px;line-height:22px;color:var(--muted);margin-top:8px;padding:0 18px}

/* what we do */
.about-band{left:0;top:1184px;width:1200px;height:536px;background:linear-gradient(90deg,#4a4440,#8a7568 50%,#5c4a42)}
.about-card{left:99px;top:1264px;width:1002px;height:376px;background:var(--white);box-shadow:0 0 0 2px rgba(255,255,255,.6)}
.about-media{left:0;top:0;width:466px;height:376px;background:linear-gradient(135deg,#c8c3b8,#8f8a7c 55%,#b5a98f)}
.play{left:198px;top:153px;width:70px;height:70px;border-radius:50%;background:rgba(0,0,0,.75);display:flex;align-items:center;justify-content:center}
.about-body{left:501px;top:40px;width:470px}
.about-body h2{font-size:34px;font-weight:700;color:var(--ink)}
.about-body p{font-size:14px;line-height:26px;color:#555;margin-top:18px}
.btn-pill{display:inline-flex;align-items:center;justify-content:center;background:var(--green);color:var(--white);font-weight:700;border-radius:24px;font-size:14px}
.about-body .btn-pill{width:128px;height:42px;margin-top:20px;font-size:13px}

/* compare */
.option{top:1965px;width:320px;height:277px;display:flex;align-items:flex-end;justify-content:center;padding-bottom:28px;font-family:"Raleway",sans-serif;font-weight:700;font-size:22px;color:var(--white)}
.opt1{left:99px;background:linear-gradient(160deg,#b79a78,#6e5a48)}
.opt2{left:440px;background:linear-gradient(160deg,#9ea7a0,#5c605a)}
.opt3{left:781px;background:linear-gradient(160deg,#c9cfd4,#7d8287)}
.arrow-btn{top:2081px;width:40px;height:40px;border-radius:50%;border:2px solid #555;display:flex;align-items:center;justify-content:center;background:var(--white)}
.btn-outline{left:416px;top:2306px;width:368px;height:62px;border:2px solid var(--green);border-radius:32px;color:var(--green);font-weight:700;font-size:15px;display:flex;align-items:center;justify-content:center}

/* how it works */
.how-band{left:0;top:2473px;width:1200px;height:700px;background:var(--light)}
.step{width:310px;text-align:center;top:2639px}
.step-circle{width:166px;height:166px;border-radius:50%;border:2px solid var(--ink);margin:0 auto;position:relative;display:flex;align-items:center;justify-content:center}
.step-num{position:absolute;right:-4px;top:4px;width:38px;height:38px;border-radius:50%;background:var(--ink);color:var(--white);font-weight:700;font-size:18px;display:flex;align-items:center;justify-content:center}
.step h3{font-size:22px;font-weight:700;margin-top:30px;color:var(--ink)}
.step p{font-size:13px;line-height:24px;color:var(--muted);margin-top:10px;padding:0}
.chev{top:2700px}
.how-btn{left:515px;top:2970px;width:170px;height:49px;font-size:16px}

/* footer */
.footer-shape{left:0;top:3050px}
.footer{left:0;top:3140px;width:1200px;height:389px;background:var(--ink);color:var(--white)}
.footer-brand{left:97px;top:3306px;width:270px;font-family:"Raleway",sans-serif;font-weight:700;font-size:28px;color:var(--white);display:flex;align-items:center;gap:10px;white-space:nowrap}
.footer-brand .brand-mark{background:var(--white);width:16px;height:16px}
.foot-col h4{font-size:17px;font-weight:700;letter-spacing:.3px;color:var(--white)}
.foot-col ul{list-style:none;margin-top:22px}
.foot-col li{font-size:13px;line-height:27px;color:#e6e6e6}
.foot-col p{font-size:13px;line-height:22px;color:#e6e6e6;margin-top:22px}
.email-field{width:253px;height:34px;background:var(--white);color:#777;font-size:13px;padding-left:12px;display:flex;align-items:center;margin-top:14px}
.foot-col .btn-pill{width:100px;height:30px;font-size:12px;margin-top:18px}
.contact-row{display:flex;gap:18px;font-size:13px;line-height:22px;color:#e6e6e6;margin-top:20px}
.contact-row svg{flex:none;margin-top:3px}
.foot-rule{left:97px;top:3452px;width:1006px;height:1px;background:#3a3436}
.copyright{left:97px;top:3482px;font-size:13px;color:#ddd}
.social{right:97px;top:3475px;display:flex;gap:10px}
.social span{width:28px;height:28px;border-radius:50%;border:1px solid #ccc}
</style>
</head>
<body>

<header class="site-header abs">
  <div class="brand abs"><span class="brand-mark"></span>Maple Home Loans</div>
  <div class="top-contact abs">
    <span><svg width="16" height="16" viewBox="0 0 24 24"><path fill="#71aa3d" d="M6.6 10.8a15.1 15.1 0 0 0 6.6 6.6l2.2-2.2a1 1 0 0 1 1-.25 11.4 11.4 0 0 0 3.6.6 1 1 0 0 1 1 1V20a1 1 0 0 1-1 1A17 17 0 0 1 3 4a1 1 0 0 1 1-1h3.5a1 1 0 0 1 1 1c0 1.25.2 2.45.6 3.6a1 1 0 0 1-.25 1z"/></svg>1 800 555 0142</span>
    <span>|</span>
    <span><svg width="16" height="14" viewBox="0 0 24 18"><rect width="24" height="18" rx="2" fill="#71aa3d"/><path d="M1 2l11 8 11-8" stroke="#fff" stroke-width="2" fill="none"/></svg>info@maplehomeloans.com</span>
  </div>
  <nav class="main-nav abs">
    <span class="active">HOME</span><span>ABOUT US</span><span>SPEAK TO BROKER</span><span>ARTICLES</span><span>CONTACT US</span>
    <svg width="16" height="16" viewBox="0 0 24 24"><circle cx="10" cy="10" r="7" stroke="#222" stroke-width="3" fill="none"/><path d="M15 15l7 7" stroke="#222" stroke-width="3"/></svg>
  </nav>
</header>

<section class="hero abs" role="img" aria-label="Photo of a smiling family of four sitting together on a sofa at home"></section>
<h1 class="hero-title abs">MAPLE HOME LOANS</h1>
<p class="hero-sub abs">At vero eos et accusamus et iusto oigni</p>
<div class="search abs">
  <div class="search-input"><svg width="12" height="16" viewBox="0 0 12 16"><path d="M6 0a6 6 0 0 0-6 6c0 4.5 6 10 6 10s6-5.5 6-10a6 6 0 0 0-6-6zm0 8.5A2.5 2.5 0 1 1 6 3.5a2.5 2.5 0 0 1 0 5z" fill="#333"/></svg>Enter a Location or PostCode</div>
  <div class="search-btn">FIND BROKER</div>
</div>
<div class="dots abs"><span></span><span></span><span></span><span></span></div>
<svg class="hero-curve abs" width="1200" height="62" viewBox="0 0 1200 62">
  <path d="M0 10 Q600 80 1200 0 L1200 62 L0 62 Z" fill="#fff"/>
  <path d="M0 10 Q600 80 1200 0" stroke="#71aa3d" stroke-width="5" fill="none"/>
</svg>

<h2 class="section-title abs" style="top:684px">WELCOME TO MAPLE HOME LOANS</h2>
<p class="section-text abs" style="top:746px">At vero eos et accusamus et iusto odio dignissimos ducimus qui blanditiis praesentium voluptatum deleniti atque corrupti quos dolores et quas molestias excepturi sint occaecati cupiditate non provident, similique sunt in culp</p>

<div class="feature abs" style="left:99px">
  <div class="feature-icon"><svg width="44" height="44" viewBox="0 0 24 24"><circle cx="12" cy="8" r="4.5" fill="#fff"/><path d="M3 22c0-5 4-8 9-8s9 3 9 8z" fill="#fff"/></svg></div>
  <h3>Local experts</h3><p>Nemo enim ipsam voluptatequ ia volu ptas sit asperna</p>
</div>
<div class="feature abs" style="left:355px">
  <div class="feature-icon"><svg width="50" height="44" viewBox="0 0 26 22"><ellipse cx="11" cy="9" rx="9.5" ry="7.5" fill="none" stroke="#fff" stroke-width="2"/><path d="M5 15l-2 5 6-3" fill="#fff"/><path d="M18 6c4 1 6 4 6 6.5 0 2-1 3.5-2.5 4.5l1 4-4-2.5" fill="none" stroke="#fff" stroke-width="2"/></svg></div>
  <h3>Trusted advice</h3><p>Nemo enim ipsam voluptatequ ia volu ptas sit asperna</p>
</div>
<div class="feature abs" style="left:612px">
  <div class="feature-icon"><svg width="44" height="44" viewBox="0 0 24 24"><circle cx="10" cy="10" r="6.5" stroke="#fff" stroke-width="3" fill="none"/><path d="M15 15l6 6" stroke="#fff" stroke-width="3.5" stroke-linecap="round"/></svg></div>
  <h3>Find a broker</h3><p>Nemo enim ipsam voluptatequ ia volu ptas sit asperna</p>
</div>
<div class="feature abs" style="left:868px">
  <div class="feature-icon"><svg width="40" height="44" viewBox="0 0 20 24"><rect x="1" y="1" width="18" height="22" rx="2" fill="none" stroke="#fff" stroke-width="2"/><rect x="4" y="4" width="12" height="5" fill="#fff"/><g fill="#fff"><rect x="4" y="11" width="3" height="3"/><rect x="8.5" y="11" width="3" height="3"/><rect x="13" y="11" width="3" height="3"/><rect x="4" y="15.5" width="3" height="3"/><rect x="8.5" y="15.5" width="3" height="3"/><rect x="13" y="15.5" width="3" height="3"/></g></svg></div>
  <h3>Calculators &amp; tools</h3><p>Nemo enim ipsam voluptatequ ia volu ptas sit asperna</p>
</div>

<section class="about-band abs" role="img" aria-label="Blurred photo of a couple reviewing paperwork together"></section>
<div class="about-card abs">
  <div class="about-media abs" role="img" aria-label="Video still of a couple meeting a broker in a bright living room"></div>
  <div class="play abs"><svg width="26" height="28" viewBox="0 0 26 28"><path d="M4 2l20 12L4 26z" fill="#fff"/></svg></div>
  <div class="about-body abs">
    <h2>WHAT WE DO</h2>
    <p>Nam libero tempore, cum soluta nobis est eligendi optio cumque nihil imp edit quo minus id quod maxime placeat facere possi.</p>
    <p>Monis voluptas assumenda est, omnis dolor repellendus. Temporibus aut emqu ibusdam et aut officiis debitis aut rerum necessitatibus saepe eveni et ut et volu ptates repudiandae sint et molestiae non recusandae. Itaque earum rerum hic tenetur a sapiente delec.</p>
    <span class="btn-pill">READ MORE</span>
  </div>
</div>

<h2 class="section-title abs" style="top:1804px">COMPARE HOME LOAN OPTIONS</h2>
<p class="section-text abs" style="top:1870px">At vero eos et accusamus et iusto odio dignissimos ducimus qui blanditiis praesentium voluptatum deleniti atque corrupti quos dolores et quas molestias excepturi sint occaecati cupiditate non provident, similique sunt in culp</p>
<div class="arrow-btn abs" style="left:27px"><svg width="10" height="16" viewBox="0 0 10 16"><path d="M8 2L2 8l6 6" stroke="#333" stroke-width="2" fill="none"/></svg></div>
<div class="option opt1 abs" role="img" aria-label="Photo of a smiling couple discussing refinancing">Refinancing a loan</div>
<div class="option opt2 abs" role="img" aria-label="Photo of a couple planning a property investment">Investing in Property</div>
<div class="option opt3 abs" role="img" aria-label="Photo of first home buyers meeting an adviser">Buying Your First Home</div>
<div class="arrow-btn abs" style="left:1126px"><svg width="10" height="16" viewBox="0 0 10 16"><path d="M2 2l6 6-6 6" stroke="#333" stroke-width="2" fill="none"/></svg></div>
<div class="btn-outline abs">COMPARE YOUR HOME LOAN OPTIONS</div>

<section class="how-band abs"></section>
<h2 class="section-title abs" style="top:2555px">HOW IT WORKS</h2>
<div class="step abs" style="left:76px">
  <div class="step-circle"><svg width="70" height="70" viewBox="0 0 24 24"><path d="M4 20l1-5L16 4l4 4L9 19z" fill="#71aa3d"/><path d="M3 21l1.5-4 2.5 2.5z" fill="#71aa3d"/></svg><span class="step-num">1</span></div>
  <h3>Apply Now</h3><p>At vero eos et accusamus et iusto odio digniss imos ducimus qui blanditiis praesenp</p>
</div>
<svg class="chev abs" style="left:395px" width="44" height="44" viewBox="0 0 44 44"><path d="M6 8l14 14L6 36M22 8l14 14-14 14" stroke="#c4c4c4" stroke-width="4" fill="none"/></svg>
<div class="step abs" style="left:443px">
  <div class="step-circle"><svg width="72" height="66" viewBox="0 0 24 22"><rect x="2" y="4" width="16" height="16" rx="2" fill="none" stroke="#71aa3d" stroke-width="2.5"/><path d="M6 11l4 4L22 2" stroke="#71aa3d" stroke-width="3.5" fill="none"/></svg><span class="step-num">2</span></div>
  <h3>Verify &amp; Approve</h3><p>At vero eos et accusamus et iusto odio digniss imos ducimus qui blanditiis praes</p>
</div>
<svg class="chev abs" style="left:758px" width="44" height="44" viewBox="0 0 44 44"><path d="M6 8l14 14L6 36M22 8l14 14-14 14" stroke="#c4c4c4" stroke-width="4" fill="none"/></svg>
<div class="step abs" style="left:807px">
  <div class="step-circle"><svg width="80" height="50" viewBox="0 0 32 20"><rect x="1" y="1" width="30" height="18" rx="1" fill="#71aa3d"/><rect x="4" y="4" width="24" height="12" fill="none" stroke="#fff" stroke-width="1.2"/><circle cx="16" cy="10" r="4.5" fill="#fff"/><text x="16" y="12.7" font-size="7" text-anchor="middle" fill="#71aa3d" font-family="Open Sans,sans-serif" font-weight="700">1</text></svg><span class="step-num">3</span></div>
  <h3>Receive your Money</h3><p>At vero eos et accusamus et iusto odio digniss imos ducimus qui blanditiis praes</p>
</div>
<span class="btn-pill how-btn abs">GET STARTED</span>

<svg class="footer-shape abs" width="1200" height="100" viewBox="0 0 1200 100">
  <path d="M0 0 Q600 110 1200 0 L1200 100 L0 100 Z" fill="#130e10"/>
  <path d="M0 4 Q600 98 1200 4" stroke="#71aa3d" stroke-width="6" fill="none"/>
  <path d="M0 14 Q600 104 1200 14 L1200 100 L0 100 Z" fill="#130e10"/>
</svg>
<footer class="footer abs"></footer>
<div class="footer-brand abs"><span class="brand-mark"></span>Maple Home Loans</div>

<div class="foot-col abs" style="left:398px;top:3228px">
  <h4>QUICK LINKS</h4>
  <ul><li>Customer Log In</li><li>About Us</li><li>How It Works</li><li>FAQ's</li><li>Blog</li><li>Contact Us</li></ul>
</div>
<div class="foot-col abs" style="left:567px;top:3228px;width:260px">
  <h4>NEWSLETTER SUBSCRIPTION</h4>
  <p>Register your Email Address to get Information about us</p>
  <div class="email-field">Email Address</div>
  <span class="btn-pill">SUBSCRIBE</span>
</div>
<div class="foot-col abs" style="left:880px;top:3228px;width:240px">
  <h4>CONTACT US</h4>
  <div class="contact-row" style="margin-top:28px"><svg width="12" height="16" viewBox="0 0 12 16"><path d="M6 0a6 6 0 0 0-6 6c0 4.5 6 10 6 10s6-5.5 6-10a6 6 0 0 0-6-6zm0 8.5A2.5 2.5 0 1 1 6 3.5a2.5 2.5 0 0 1 0 5z" fill="#fff"/></svg><span>Lindenlaan 12, 4611 AB Bergen Nederland</span></div>
  <div class="contact-row"><svg width="14" height="14" viewBox="0 0 24 24"><path fill="#fff" d="M6.6 10.8a15.1 15.1 0 0 0 6.6 6.6l2.2-2.2a1 1 0 0 1 1-.25 11.4 11.4 0 0 0 3.6.6 1 1 0 0 1 1 1V20a1 1 0 0 1-1 1A17 17 0 0 1 3 4a1 1 0 0 1 1-1h3.5a1 1 0 0 1 1 1c0 1.25.2 2.45.6 3.6a1 1 0 0 1-.25 1z"/></svg><span>1 800 555 0142</span></div>
  <div class="contact-row"><svg width="16" height="12" viewBox="0 0 24 18"><rect width="24" height="18" rx="2" fill="#fff"/><path d="M1 2l11 8 11-8" stroke="#130e10" stroke-width="2" fill="none"/></svg><span>info@maplehomeloans.com</span></div>
</div>

<div class="foot-rule abs"></div>
<p class="copyright abs">Copyrights © 2018, Maple home loans.&nbsp; All rights reserved.</p>
<div class="social abs"><span></span><span></span><span></span><span></span></div>

</body>
</html>
```